Business Cards for new orthopaedic surgery practice

My husband and I are starting our own orthopaedic surgery practice. We are looking for a business card that is uniform, but one will have my name/title and the other will have his. You can just create one design with my name on it for now. But when I choose your design as the winning design I will ask that you add another copy with his name/title.

We are looking for classy, simple, elite all in one. We like dark blues/a little gold/yellow. Something that goes with our logo. We want our logo incorporated. Here is all the info you need:
Business name: RV Bone & Vitality Center
Location: 38517 North Willowmere Ave
Maple Hollow, FL 33987
Phone: 954-218-4063
Fax: 954-582-7341
Email: info@myrvbonecare.example

Names: Lydia Vance, M.D.
Board Certified Hand and Upper Extremity Surgeon

Ebo Dansu, M.D.
Board Certified Hip & Knee Replacement/General Orthopaedic Surgeon

Can decide what you want to put on the back. Maybe a slogan:
Grounded in Care. Built Around You

I am just going to upload our logo. The only thing is if we select you as the winning design, the location, and phone numbers may change. We will need your help to update that once fully solidified.

Industry/Entity Type

Medical

Contact Information for Business Card

Colors
0054AA
0677BA
7BADD7
CADEEF
E8F1F8
0094D4
00A9DD
6FCCEA
C7EBF8
E9F6FB

Requirements
Must have
• class, appeal,
Should not have
• We want to air on the side of masculine if we are looking at masculine vs. feminine feel. But we still want it classy, sophisticated, and something we will love

```html
<!DOCTYPE html>
<html lang="en">
<head>
<meta charset="utf-8">
<title>RV Bone &amp; Vitality Center – Business Card</title>
<link href="https://fonts.googleapis.com/css2?family=Cinzel:wght@700&family=Arimo:wght@400&display=swap" rel="stylesheet">
<style>
  :root {
    --page: #e4e4e4;
    --navy-top: #2d3f69;
    --navy-bottom: #1d2b58;
    --navy-ink: #1f2d5a;
    --gold: #c9a25c;
    --white: #ffffff;
    --ghost: #3c5488;
    --slogan: #27355f;
  }
  * { margin: 0; padding: 0; box-sizing: border-box; }
  html, body { width: 1200px; height: 1200px; overflow: hidden; background: var(--page); }
  .sheet { position: relative; width: 1200px; height: 1200px; }

  .card {
    position: absolute; left: 264px; width: 688px; height: 393px; overflow: hidden;
  }
  .card--front { top: 159px; background: linear-gradient(180deg, var(--navy-top), var(--navy-bottom)); }
  .card--back { top: 653px; left: 262px; background: var(--white); }

  .brand-mark {
    position: absolute; left: 48px; top: 30px; width: 106px; height: 106px;
    border: 2px solid var(--white); border-radius: 50%;
    display: flex; align-items: center; justify-content: center; text-align: center;
    font-family: "Cinzel", serif; font-weight: 700; font-size: 11px; line-height: 1.35;
    color: var(--white); padding: 10px;
  }

  .ghost-name {
    position: absolute; right: 28px; top: 130px; text-align: right;
    font-family: "Cinzel", serif; font-weight: 700; font-size: 50px; line-height: 1.05;
    color: var(--ghost); opacity: .55;
  }

  .doctor-name {
    position: absolute; left: 44px; top: 152px;
    font-family: "Cinzel", serif; font-weight: 700; font-size: 24.5px; color: var(--gold);
    letter-spacing: .4px;
  }
  .info {
    position: absolute; left: 44px;
    font-family: "Arimo", sans-serif; font-size: 15.5px; line-height: 20px; color: var(--white);
  }
  .info--title { top: 183px; }
  .info--address { top: 233px; }

  .contacts { position: absolute; left: 45px; top: 287px; list-style: none; }
  .contacts li {
    display: flex; align-items: center; height: 20.5px;
    font-family: "Arimo", sans-serif; font-size: 15.5px; color: var(--white);
  }
  .contacts svg { width: 14px; height: 14px; margin-right: 10px; fill: var(--gold); flex: none; }

  .back-mark {
    position: absolute; left: 214px; top: 50px; width: 260px; height: 240px;
    display: flex; flex-direction: column; align-items: center; justify-content: center; text-align: center;
    font-family: "Cinzel", serif; font-weight: 700; font-size: 34px; line-height: 1.2; color: var(--navy-ink);
  }
  .slogan {
    position: absolute; left: 0; right: 0; top: 335px; text-align: center;
    font-family: "Arimo", sans-serif; font-size: 15px; letter-spacing: 3.2px; color: var(--slogan);
  }
</style>
</head>
<body>
<main class="sheet">
  <section class="card card--front" aria-label="Business card front">
    <div class="brand-mark">RV Bone &amp; Vitality Center</div>
    <div class="ghost-name" aria-hidden="true">RV BONE &amp;<br>VITALITY<br>CENTER</div>

    <h1 class="doctor-name">LYDIA VANCE, M.D.</h1>
    <p class="info info--title">Board Certified Hand and<br>Upper Extremity Surgeon</p>
    <p class="info info--address">38517 North Willowmere Ave<br>Maple Hollow, FL 33987</p>

    <ul class="contacts">
      <li><svg viewBox="0 0 24 24" aria-hidden="true"><path d="M6.6 10.8a15 15 0 0 0 6.6 6.6l2.2-2.2c.3-.3.7-.4 1-.2 1.1.4 2.3.6 3.6.6.6 0 1 .4 1 1V20c0 .6-.4 1-1 1A17 17 0 0 1 3 4c0-.6.4-1 1-1h3.5c.6 0 1 .4 1 1 0 1.3.2 2.5.6 3.6.1.3 0 .7-.2 1z"/></svg>954-218-4063</li>
      <li><svg viewBox="0 0 24 24" aria-hidden="true"><path d="M6 2h9l3 3v4H6z M3 10h18v9h-3v3H6v-3H3z M8 15v5h8v-5z"/></svg>954-582-7341</li>
      <li><svg viewBox="0 0 24 24" aria-hidden="true"><path d="M2 5h20v14H2z M4 7v.5l8 5.5 8-5.5V7z" fill-rule="evenodd"/></svg>info@myrvbonecare.example</li>
      <li><svg viewBox="0 0 24 24" aria-hidden="true"><path d="M12 2a10 10 0 1 0 0 20 10 10 0 0 0 0-20zm-1 17.9A8 8 0 0 1 4.1 11H7c0 2 1 3 2 3v2c0 1 1 2 2 2zm6.9-2.5c-.3-.8-1-1.4-1.9-1.4h-1v-3c0-.6-.4-1-1-1H8v-2h2c.6 0 1-.4 1-1V7h2c1.1 0 2-.9 2-2v-.4a8 8 0 0 1 2.9 12.8z"/></svg>www.myrvbonecare.example</li>
    </ul>
  </section>

  <section class="card card--back" aria-label="Business card back">
    <div class="back-mark">RV Bone &amp;<br>Vitality<br>Center</div>
    <p class="slogan">GROUNDED IN CARE. BUILT AROUND YOU</p>
  </section>
</main>
</body>
</html>
```